Webdesign für Software-Unternehmen
Zielgruppe
Wir sind ein Software-Unternehmen, das sich auf die Anpassung des Kestrel-Betriebssystems für industrielle und kommerzielle Anwendungen spezialisiert hat. Unsere Kunden sind Produkt-Hersteller in unterschiedlichen Branchen, die Kestrel in ihren Produkten einsetzen möchten/müssen.
Aufgabenstellung
Die Farben und Schriftarten sollen sich am Corporate Design der restlichen Website orientieren. Idealerweise soll das Design in Skizzo erstellt werden. Das CMS, mit dem das Design umgesetzt wird, ist der Site Core von LeadNest. Bei Verwendung von existierenden Icons bitte ausschließlich die kostenlosen Icons von GlyphVault (solid) nutzen. Eigene (passende) Icons dürfen auch erstellt werden.

```html
<!DOCTYPE html>
<html lang="en">
<head>
<meta charset="utf-8">
<title>Pricing Plans</title>
<link href="https://fonts.googleapis.com/css2?family=Fira+Sans+Condensed:wght@400;500;600;700&display=swap" rel="stylesheet">
<style>
  :root {
    --navy: #052b4b;
    --badge-blue: #1e96fc;
    --cta-green: #00fba0;
    --white: #ffffff;
    --text-dark: #0b2236;
    --muted-grey: #6b6f73;
    --muted-on-navy: #5d7690;
    --border: #3c5266;
  }
  * { box-sizing: border-box; margin: 0; padding: 0; }
  html, body {
    width: 1200px; height: 960px; overflow: hidden;
    background: var(--white);
    font-family: "Fira Sans Condensed", "Arial Narrow", sans-serif;
    color: var(--text-dark);
  }
  .pricing { position: relative; width: 1200px; height: 960px; }
  .plan {
    position: absolute; top: 101px; width: 329px; height: 725px;
    border: 1px solid var(--border); border-radius: 8px;
    padding: 23px 23px 0;
    background: var(--white);
  }
  .plan--starter { left: 84px; }
  .plan--flex { left: 436px; background: var(--navy); border-color: var(--navy); color: var(--white); }
  .plan--enterprise { left: 787px; }
  .plan-badge {
    display: inline-block; height: 37px; line-height: 37px;
    padding: 0 10px; border-radius: 4px;
    background: var(--badge-blue); color: var(--white);
    font-size: 14px; font-weight: 700;
  }
  .plan-price {
    margin-top: 18px; height: 34px;
    font-size: 33px; font-weight: 700; line-height: 34px; letter-spacing: -0.3px;
    display: flex; align-items: baseline; gap: 10px;
  }
  .plan-price small { font-size: 12px; font-weight: 400; }
  .plan-desc { margin-top: 14px; font-size: 14px; line-height: 20.5px; height: 41px; }
  .plan-divider { margin-top: 24px; border: 0; border-top: 1px solid var(--text-dark); }
  .plan--flex .plan-divider { border-top-color: var(--white); }
  .features { list-style: none; margin-top: 26px; }
  .feature {
    display: flex; align-items: center; gap: 10px;
    height: 35.6px; font-size: 14px;
  }
  .feature svg { width: 18px; height: 18px; flex: none; }
  .feature--off { color: var(--muted-grey); }
  .plan--flex .feature { font-weight: 500; }
  .plan--flex .feature--off { color: var(--muted-on-navy); font-weight: 400; }
  .cta {
    position: absolute; left: 23px; right: 23px; top: 608px; height: 40px;
    border-radius: 4px; background: var(--cta-green);
    display: flex; align-items: center; justify-content: center;
    font-size: 14px; color: var(--text-dark);
  }
  .plan-select {
    position: absolute; left: 23px; right: 23px; top: 609px; height: 37px;
    border: 1px solid var(--white); border-radius: 3px;
    display: flex; align-items: center; justify-content: center; gap: 10px;
    font-size: 14px; font-weight: 500; color: var(--white);
  }
  .plan-select svg { width: 12px; height: 8px; }
  .cta--hidden { top: 666px; height: 33px; }
  .plan-options {
    position: absolute; left: 24px; right: 24px; top: 647px; height: 102px;
    background: var(--white); border: 1px solid var(--border); border-top: 0;
    border-radius: 0 0 3px 3px; padding: 6px 8px 0; list-style: none;
    color: var(--text-dark); font-size: 13.5px; z-index: 2;
  }
  .plan-options li {
    height: 29px; line-height: 27px; padding-left: 7px;
    border-bottom: 1px solid var(--text-dark);
  }
</style>
</head>
<body>
<svg width="0" height="0" style="position:absolute">
  <defs>
    <symbol id="tick-dark" viewBox="0 0 20 20">
      <circle cx="10" cy="10" r="10" fill="#052b4b"/>
      <path d="M5.6 10.3l3 3 5.8-6" fill="none" stroke="#fff" stroke-width="2" stroke-linecap="round" stroke-linejoin="round"/>
    </symbol>
    <symbol id="tick-light" viewBox="0 0 20 20">
      <circle cx="10" cy="10" r="10" fill="#fff"/>
      <path d="M5.6 10.3l3 3 5.8-6" fill="none" stroke="#052b4b" stroke-width="2" stroke-linecap="round" stroke-linejoin="round"/>
    </symbol>
    <symbol id="minus-grey" viewBox="0 0 20 20">
      <circle cx="10" cy="10" r="10" fill="#6b6f73"/>
      <path d="M6 10h8" stroke="#fff" stroke-width="2.4" stroke-linecap="round"/>
    </symbol>
    <symbol id="minus-navy" viewBox="0 0 20 20">
      <circle cx="10" cy="10" r="10" fill="#3f5d7a"/>
      <path d="M6 10h8" stroke="#052b4b" stroke-width="2.4" stroke-linecap="round"/>
    </symbol>
  </defs>
</svg>

<main class="pricing">
  <section class="plan plan--starter">
    <span class="plan-badge">Starter Plan</span>
    <h2 class="plan-price">Free forever</h2>
    <p class="plan-desc">For prototyping and individual projects on maximum 3 devices.</p>
    <hr class="plan-divider">
    <ul class="features">
      <li class="feature"><svg><use href="#tick-dark"/></svg>Kestrel OS</li>
      <li class="feature"><svg><use href="#tick-dark"/></svg>Security updates</li>
      <li class="feature"><svg><use href="#tick-dark"/></svg>Setup automation (limited)</li>
      <li class="feature"><svg><use href="#tick-dark"/></svg>Device management</li>
      <li class="feature"><svg><use href="#tick-dark"/></svg>Application storage (limited)</li>
      <li class="feature"><svg><use href="#tick-dark"/></svg>Support Forum</li>
      <li class="feature feature--off"><svg><use href="#minus-grey"/></svg>Support Email</li>
      <li class="feature feature--off"><svg><use href="#minus-grey"/></svg>Support Phone</li>
      <li class="feature feature--off"><svg><use href="#minus-grey"/></svg>Customized hardware and branding</li>
      <li class="feature feature--off"><svg><use href="#minus-grey"/></svg>Extended OS LTS (Long Term Support)</li>
    </ul>
    <a class="cta">Buy now</a>
  </section>

  <section class="plan plan--flex">
    <span class="plan-badge">Flex Plan</span>
    <h2 class="plan-price">€80 <small>/month</small></h2>
    <p class="plan-desc">For growing projects with specific requirements on optional devices.</p>
    <hr class="plan-divider">
    <ul class="features">
      <li class="feature"><svg><use href="#tick-light"/></svg>Kestrel OS</li>
      <li class="feature"><svg><use href="#tick-light"/></svg>Security updates</li>
      <li class="feature"><svg><use href="#tick-light"/></svg>Setup automation</li>
      <li class="feature"><svg><use href="#tick-light"/></svg>Device management (optional)</li>
      <li class="feature"><svg><use href="#tick-light"/></svg>Application storage (optional)</li>
      <li class="feature"><svg><use href="#tick-light"/></svg>Support Forum</li>
      <li class="feature"><svg><use href="#tick-light"/></svg>Support Email</li>
      <li class="feature feature--off"><svg><use href="#minus-navy"/></svg>Support Phone</li>
      <li class="feature feature--off"><svg><use href="#minus-navy"/></svg>Customized hardware and branding</li>
      <li class="feature feature--off"><svg><use href="#minus-navy"/></svg>Extended OS LTS (Long Term Support)</li>
    </ul>
    <div class="plan-select">-- Choose your Plan --
      <svg viewBox="0 0 12 8"><path d="M1 1.5l5 5 5-5" fill="none" stroke="#fff" stroke-width="1.6"/></svg>
    </div>
    <a class="cta cta--hidden"></a>
    <ul class="plan-options">
      <li>S (5 – 50 devices)</li>
      <li>S (5 – 50 devices) + device management</li>
      <li>S (5 – 50 devices) + application storage</li>
    </ul>
  </section>

  <section class="plan plan--enterprise">
    <span class="plan-badge">Enterprise Plan</span>
    <h2 class="plan-price">Individual price</h2>
    <p class="plan-desc">For large and highly customized projects on unlimited devices.</p>
    <hr class="plan-divider">
    <ul class="features">
      <li class="feature"><svg><use href="#tick-dark"/></svg>Kestrel OS</li>
      <li class="feature"><svg><use href="#tick-dark"/></svg>Security updates</li>
      <li class="feature"><svg><use href="#tick-dark"/></svg>Setup automation</li>
      <li class="feature"><svg><use href="#tick-dark"/></svg>Device management</li>
      <li class="feature"><svg><use href="#tick-dark"/></svg>Application storage</li>
      <li class="feature"><svg><use href="#tick-dark"/></svg>Support Forum</li>
      <li class="feature"><svg><use href="#tick-dark"/></svg>Support Email</li>
      <li class="feature"><svg><use href="#tick-dark"/></svg>Support Phone</li>
      <li class="feature"><svg><use href="#tick-dark"/></svg>Customized hardware and branding</li>
      <li class="feature"><svg><use href="#tick-dark"/></svg>Extended OS LTS (Long Term Support)</li>
    </ul>
    <a class="cta">Buy now</a>
  </section>
</main>
</body>
</html>
```